Graphic Design Project

We make rose petal jelly from old fashioned english roses. The jelly is sweet eaten with scones and clotted cream or as a filling in a victoria sandwich, as a topping on ice cream or thick set yogurt.
The image of the product is luxurious and decadent and very english.
We need a design for a label which has a picture of an old fashioned rose (rosa mundi or a compte de chambard) The rose must stand out clearly so the jelly is not confused with other fruit jams. The overall colour of the label should be pink and soft, with white or dark pink writing. The label needs to be fridge proof.

We also need a security strip to fit on the lid of the jar.

We need the following information on the label.
Name of our company-"Meadow Crown"
Name of Product-"Rose Petal Jelly"
Sales pitch-"With whole petals-a taste of summer, delicious on scones, as a filling in sponge cake, as a topping on ice cream or yogurt."
INGREDIENTS: Sugar, water, rose petals, lemon juice, natural jelling agent (agar-agar)
STORAGE: Store in a cool dry place, once opened keep refrigerated and consume within 4 weeks.
BEST BEFORE: See base

200g
Produced by:
MEADOW CROWN
The Larches
Pardew Lane
Ashcombe
Mardenshire
GL17 4RX
The label must have room for a bar code. The size of label approx 8-10cm long 5cm wide.
Updates

Hi

Just been looking at the Hartwell and Brace site and the labels they have there have the up market feel I am trying to convey. Hope that helps, its classy but not twee.

Thanks

Thanks for all submissions. I would be grateful if you googled images for 'Colourful and expensive biscuits at Hartwell Brace' The designs on the tins are the image we are trying to create. The colours are quite strong.

Thanks

Target Market(s)

older well off people who visit garden centres

Industry/Entity Type

Security

Requirements
Must have
• All writen info above and picture of old fashioned rose prferably rose a mundi. Luxury feel, very english, to appeal to older market
Pink colour sheme
Should not have
• dark or manly colours

```html
<!DOCTYPE html>
<html lang="en">
<head>
<meta charset="utf-8">
<title>Meadow Crown Rose Petal Jelly Label</title>
<link rel="stylesheet" href="https://fonts.googleapis.com/css2?family=Sorts+Mill+Goudy&display=swap">
<style>
  :root {
    --label-magenta: #d6045f;
    --soft-pink: #f7a3d2;
    --blush-pink: #f5b3d9;
    --white: #ffffff;
    --info-plum: #8a1748;
    --rose-red: #d8102a;
    --rose-deep: #7e0514;
    --ink: #111111;
  }
  * { margin: 0; padding: 0; box-sizing: border-box; }
  html, body { width: 1200px; height: 750px; overflow: hidden; background: var(--white); }
  .label {
    position: relative;
    width: 1200px;
    height: 750px;
    font-family: "Sorts Mill Goudy", "Goudy Old Style", Georgia, serif;
  }
  .front-panel {
    position: absolute;
    left: 0; top: 0;
    width: 797px; height: 750px;
    background: var(--label-magenta);
  }
  .brand-name {
    position: absolute; left: 0; width: 810px; top: 36px;
    text-align: center; font-size: 54px; line-height: 1; color: var(--soft-pink);
    font-weight: 400;
  }
  .product-name {
    position: absolute; left: 0; width: 825px; top: 112px;
    text-align: center; font-size: 74px; line-height: 1; color: var(--white);
    font-weight: 400;
  }
  .tagline {
    position: absolute; left: 0; width: 815px; top: 200px;
    text-align: center; font-size: 26px; line-height: 1; color: var(--soft-pink);
  }
  .rose-art {
    position: absolute; left: 272px; top: 280px;
    width: 270px; height: 238px;
  }
  .serving-ideas {
    position: absolute; left: 0; width: 830px; top: 582px;
    text-align: center; font-size: 31.5px; line-height: 40px; color: var(--blush-pink);
  }
  .net-weight {
    position: absolute; left: 608px; top: 696px;
    font-size: 33px; line-height: 1; color: var(--white);
  }
  .info-panel {
    position: absolute; left: 817px; top: 0;
    width: 383px; height: 750px;
    color: var(--info-plum);
  }
  .info-block {
    position: absolute; left: 0;
    font-size: 23.6px; line-height: 29px;
    white-space: nowrap;
  }
  .info-block.ingredients { top: 28px; }
  .info-block.storage { top: 151px; }
  .info-block.best-before { top: 278px; }
  .producer {
    position: absolute; left: 0; top: 378px;
    font-size: 30px; line-height: 35px;
    font-style: normal;
    white-space: nowrap;
  }
  .barcode-space {
    position: absolute; left: 1001px; top: 636px;
    width: 175px; height: 90px;
    border: 1.5px solid var(--ink);
    padding: 20px 0 0 6px;
    font-family: Arial, Helvetica, sans-serif;
    font-size: 17px; line-height: 24px; color: var(--ink);
  }
</style>
</head>
<body>
<main class="label">
  <section class="front-panel">
    <h2 class="brand-name">Meadow Crown</h2>
    <h1 class="product-name">Rose Petal Jelly</h1>
    <p class="tagline">&quot;With whole petals its a taste of summer&rdquo;</p>

    <svg class="rose-art" viewBox="0 0 270 238" role="img" aria-label="Illustration of three red old fashioned roses">
      <defs>
        <radialGradient id="roseTone" cx="50%" cy="45%" r="55%">
          <stop offset="0%" stop-color="#7e0514"/>
          <stop offset="55%" stop-color="#d8102a"/>
          <stop offset="100%" stop-color="#e8283d"/>
        </radialGradient>
      </defs>
      <g stroke="#ffffff" stroke-width="5" fill="url(#roseTone)">
        <circle cx="68" cy="75" r="64"/>
        <circle cx="200" cy="66" r="63"/>
        <circle cx="153" cy="166" r="64"/>
      </g>
    </svg>

    <p class="serving-ideas">Delicious on scones, as a filling<br>in sponge cake, as a topping<br>on ice cream or yogurt.</p>
    <p class="net-weight">200g</p>
  </section>

  <section class="info-panel">
    <p class="info-block ingredients">INGREDIENTS:<br>Sugar, water, rose petals, lemon<br>juice, natural jelling agent (agar-agar)</p>
    <p class="info-block storage">STORAGE: Store in a cool dry<br>place, once opened keep refrigerated<br>and consume within 4 weeks.</p>
    <p class="info-block best-before">BEST BEFORE:<br>See base</p>
    <address class="producer">Produced by:<br>MEADOW CROWN<br>The Larches<br>Pardew Lane<br>Ashcombe<br>Mardenshire<br>GL17 4RX</address>
  </section>

  <div class="barcode-space">Bar<br>Code</div>
</main>
</body>
</html>
```